Luxury supplement label and packaging design

I want to bring to fruition my vision for a line of supplements my business will be coming out with. Our place in the fitness space will cater to high end/ luxury good buyers. We have a Greek theme (Brava Lune) and I would like to incorporate a Greek key pattern along the border or somewhere. I have a logo made, as well as other design concepts o could show you I have an idea for. Please contact me if you decide to take this job. Some design inspiration include brands such as Morlenti, Pardo, Vireau, Halvery, and Krestovance. I have a name for the product/s I want labels created for.

Target Market(s)

High end/ luxury buyers. Men (age 27-39) Women (21-45). Fitness activists who enjoy luxury lifestyle brands.

Industry/Entity Type

Supplement

Font styles to use
Other font styles liked:
• CSL Greek Medium, Trajan Pro

Colors
fbee3f

Requirements
Must have
• Black, white, gold color combo. Greek Key pattern on top, bottom or both borders. Logo. Name of product available upon request.
• Name of product: RUBY TIDE
• Size: image attached
• Logo: Image attached
• Product description: image attached
Nice to have
• Ask for nutrition facts. Statements that are creative and appealing on side of label, description. Greek Font, uppercase. CSL Greek Medium

```html
<!DOCTYPE html>
<html lang="en">
<head>
<meta charset="utf-8">
<title>Ruby Tide – Premium Pre Workout Label</title>
<link rel="stylesheet" href="https://fonts.googleapis.com/css2?family=Cinzel:wght@400;600;700&family=Exo+2:ital,wght@0,700;1,500&display=swap">
<style>
  :root {
    --page: #ffffff;
    --label-black: #0b0b0b;
    --label-edge: #1c1c1c;
    --gold: #fbee3f;
    --gold-deep: #c9a23a;
    --gold-dark: #8a6a1e;
    --silver: #d9d9d9;
    --soft-white: #e8e8e8;
  }
  * { margin: 0; padding: 0; box-sizing: border-box; }
  html, body {
    width: 1200px;
    height: 1072px;
    overflow: hidden;
    background: var(--page);
  }
  .canvas {
    position: relative;
    width: 1200px;
    height: 1072px;
    background: var(--page);
  }
  .label {
    position: absolute;
    left: 332px;
    top: 372px;
    width: 532px;
    height: 432px;
    background: radial-gradient(ellipse at 50% 40%, #1d1d1d 0%, var(--label-black) 70%);
    border-top: 3px solid #6e6e6e;
    overflow: hidden;
  }
  .brand-mark {
    position: absolute;
    left: 50%;
    top: 24px;
    width: 78px;
    height: 78px;
    margin-left: -39px;
    border: 3px solid var(--gold-deep);
    border-radius: 50%;
  }
  .brand-name {
    position: absolute;
    top: 114px;
    width: 100%;
    text-align: center;
    font-family: "Cinzel", serif;
    font-weight: 600;
    font-size: 19px;
    letter-spacing: 1px;
    color: var(--gold-deep);
  }
  .brand-tagline {
    position: absolute;
    top: 138px;
    width: 100%;
    text-align: center;
    font-family: "Cinzel", serif;
    font-weight: 400;
    font-size: 11.5px;
    letter-spacing: 1px;
    color: #a89a78;
  }
  .product-name {
    position: absolute;
    top: 168px;
    width: 100%;
    text-align: center;
    font-family: "Cinzel", serif;
    font-weight: 700;
    font-size: 60px;
    line-height: 1;
    letter-spacing: 1px;
    background: linear-gradient(90deg, var(--gold-deep) 0%, var(--gold) 25%, var(--silver) 50%, var(--gold) 75%, var(--gold-deep) 100%);
    -webkit-background-clip: text;
    background-clip: text;
    color: transparent;
  }
  .product-type {
    position: absolute;
    top: 254px;
    width: 100%;
    text-align: center;
    font-family: "Exo 2", sans-serif;
    font-weight: 700;
    font-size: 27px;
    color: var(--soft-white);
  }
  .count-badge {
    position: absolute;
    left: 88px;
    top: 326px;
    width: 82px;
    height: 64px;
    background: linear-gradient(160deg, var(--gold) 0%, var(--gold-deep) 100%);
    border-radius: 8px;
    transform: skewX(-8deg);
    text-align: center;
    font-family: "Exo 2", sans-serif;
    color: #111;
  }
  .count-badge .count {
    display: block;
    font-weight: 700;
    font-size: 33px;
    line-height: 40px;
  }
  .count-badge .unit {
    display: block;
    font-weight: 500;
    font-size: 12px;
  }
  .meta {
    position: absolute;
    top: 362px;
    font-family: "Exo 2", sans-serif;
    font-style: italic;
    font-weight: 500;
    font-size: 14px;
  }
  .meta-type { left: 176px; color: var(--gold); }
  .meta-weight { left: 340px; color: var(--soft-white); }
  .key-band {
    position: absolute;
    left: 0;
    top: 388px;
    width: 100%;
    height: 32px;
    border-top: 2px solid var(--gold-deep);
    border-bottom: 2px solid var(--gold-deep);
    background: linear-gradient(90deg, var(--gold-dark) 0%, var(--gold-deep) 30%, var(--gold) 50%, var(--gold-deep) 70%, var(--gold-dark) 100%);
  }
</style>
</head>
<body>
  <main class="canvas">
    <section class="label">
      <div class="brand-mark"></div>
      <p class="brand-name">BRAVA LUNE</p>
      <p class="brand-tagline">HEALTH AND FITNESS</p>
      <h1 class="product-name">RUBY TIDE</h1>
      <p class="product-type">Premium Pre Workout</p>
      <div class="count-badge">
        <span class="count">30</span>
        <span class="unit">Capsules</span>
      </div>
      <p class="meta meta-type">Dietary Supplement</p>
      <p class="meta meta-weight">Net Weight 1500g</p>
      <div class="key-band" role="img" aria-label="Gold Greek key border pattern"></div>
    </section>
  </main>
</body>
</html>
```